Business Card Design For A Renovation Contractor Company

We need a business card for a new company based in Singapore, our company name is "RB Tolvane". We are a renovation contractor that builds designs into reality. We build more of F&B restaurants, retail stores and commercial offices. We work very closely with designers. The final design should communicate to our client that we are a company that you can trust, that will plan and complete your project without giving you a headache. I like my client to remember my company as "RB". The beauty of SIMPLE is important.

Industry/Entity Type

Contractor

Requirements
Nice to have
• Black or Red base

```html
<!DOCTYPE html>
<html lang="en">
<head>
<meta charset="utf-8">
<title>RB Tolvane – Business Cards</title>
<link rel="stylesheet" href="https://fonts.googleapis.com/css2?family=PT+Sans:wght@400;700&display=swap">
<style>
  :root {
    --bg: #3b2b22;
    --red: #e41d25;
    --black: #141414;
    --charcoal: #262626;
    --white: #ffffff;
    --ink: #2a2a2a;
    --muted: #555555;
    --rule: #cfcfcf;
    --faint: #e4e4e4;
  }
  * { margin: 0; padding: 0; box-sizing: border-box; }
  html, body { width: 1200px; height: 913px; overflow: hidden; }
  body {
    position: relative;
    background: var(--bg);
    font-family: "PT Sans", Arial, sans-serif;
  }
  .card {
    position: absolute;
    width: 463px;
    height: 266px;
    overflow: hidden;
    box-shadow: 0 6px 14px rgba(0,0,0,.45);
  }
  .card--front  { left: 91px;  top: 146px; background: var(--white); }
  .card--back1  { left: 607px; top: 146px; background: linear-gradient(160deg, #3a3a3a 0%, var(--charcoal) 45%, var(--black) 100%); }
  .card--back2  { left: 91px;  top: 451px; background: var(--red); }
  .card--back3  { left: 607px; top: 450px; background: var(--white); }

  .side-strip { position: absolute; top: 0; width: 20px; height: 100%; }
  .card--front .side-strip { right: 0; }
  .card--back1 .side-strip,
  .card--back3 .side-strip { left: 0; }

  .brand {
    position: absolute;
    display: flex;
    flex-direction: column;
    align-items: center;
    white-space: nowrap;
  }
  .brand__mark {
    width: 52px; height: 52px;
    border-radius: 50%;
    border: 5px solid var(--red);
    margin-bottom: 10px;
  }
  .brand__name {
    font-size: 34px;
    font-weight: 400;
    line-height: 1;
    letter-spacing: -0.5px;
  }
  .brand__tagline {
    font-size: 12.5px;
    margin-top: 4px;
    letter-spacing: .2px;
  }
  .card--front .brand { left: 16px; top: 62px; width: 230px; }
  .card--front .brand__name { color: var(--ink); font-size: 31px; }
  .card--front .brand__tagline { color: var(--red); font-size: 11.5px; }

  .card--back1 .brand { left: 90px; top: 58px; width: 300px; }
  .card--back1 .brand__mark { border-color: var(--white); }
  .card--back1 .brand__name,
  .card--back1 .brand__tagline { color: var(--white); }

  .card--back2 .brand { left: 70px; top: 48px; width: 323px; }
  .card--back2 .brand__mark { border-color: var(--white); width: 80px; height: 80px; border-width: 6px; margin-bottom: 14px; }
  .card--back2 .brand__name { color: var(--white); font-size: 42px; }
  .card--back2 .brand__tagline { color: var(--white); font-size: 14px; }

  .divider {
    position: absolute;
    left: 259px; top: 24px;
    width: 1px; height: 212px;
    background: var(--rule);
  }
  .person { position: absolute; left: 278px; top: 34px; color: var(--ink); }
  .person__name { font-size: 21px; line-height: 1.1; }
  .person__title { font-size: 14px; }

  .contact { position: absolute; left: 278px; top: 148px; list-style: none; color: var(--muted); font-size: 11.5px; line-height: 16px; }
  .contact li { display: flex; align-items: center; gap: 5px; }
  .contact svg { width: 10px; height: 10px; fill: var(--muted); }
  .address { position: absolute; left: 278px; top: 212px; color: var(--muted); font-size: 11.5px; line-height: 15px; }

  .watermark-ring {
    position: absolute;
    left: 170px; top: -30px;
    width: 320px; height: 320px;
    border-radius: 50%;
    border: 26px solid var(--faint);
  }

  .label {
    position: absolute;
    color: var(--white);
    font-size: 29px;
  }
  .label--back1 { left: 965px; top: 92px; }
  .label--back2 { left: 127px; top: 736px; }
  .label--back3 { left: 980px; top: 734px; }
</style>
</head>
<body>

  <span class="label label--back1">Back 1</span>
  <span class="label label--back2">Back 2</span>
  <span class="label label--back3">Back 3</span>

  <section class="card card--front">
    <div class="brand">
      <span class="brand__mark"></span>
      <span class="brand__name">RB Tolvane</span>
      <span class="brand__tagline">spaces built right, on time</span>
    </div>
    <div class="divider"></div>
    <div class="person">
      <p class="person__name">Your namehere</p>
      <p class="person__title">Director</p>
    </div>
    <ul class="contact">
      <li><svg viewBox="0 0 10 10"><path d="M2 0.5l2 2-1 1.2c.6 1.3 1.6 2.3 2.9 2.9l1.2-1 2 2-1.3 1.9C4.5 9.3.7 5.5.1 1.8z"/></svg>014.527.3860</li>
      <li><svg viewBox="0 0 10 10"><rect x="0" y="2" width="10" height="6"/><path d="M0 2l5 3.5L10 2" fill="none" stroke="#fff" stroke-width=".8"/></svg>info@rbtolvane.com</li>
      <li><svg viewBox="0 0 10 10"><circle cx="5" cy="5" r="4.6"/></svg>www.rbtolvane.com</li>
    </ul>
    <p class="address">Suite 000, RB building,<br>Cityname, country name</p>
    <svg class="side-strip" viewBox="0 0 20 266" preserveAspectRatio="none">
      <rect width="20" height="266" fill="#141414"/>
      <polygon points="20,55 0,80 0,115 20,90" fill="#e41d25"/>
      <polygon points="20,150 0,175 0,210 20,185" fill="#e41d25"/>
    </svg>
  </section>

  <section class="card card--back1">
    <svg class="side-strip" viewBox="0 0 20 266" preserveAspectRatio="none">
      <rect width="20" height="266" fill="#141414"/>
      <polygon points="0,150 20,175 20,266 0,266" fill="#e41d25"/>
    </svg>
    <div class="brand">
      <span class="brand__mark"></span>
      <span class="brand__name">RB Tolvane</span>
      <span class="brand__tagline">spaces built right, on time</span>
    </div>
  </section>

  <section class="card card--back2">
    <div class="brand">
      <span class="brand__mark"></span>
      <span class="brand__name">RB Tolvane</span>
      <span class="brand__tagline">spaces built right, on time</span>
    </div>
  </section>

  <section class="card card--back3">
    <span class="watermark-ring"></span>
    <svg class="side-strip" viewBox="0 0 20 266" preserveAspectRatio="none">
      <rect width="20" height="266" fill="#e41d25"/>
      <polygon points="0,0 20,0 20,40 0,65" fill="#141414"/>
      <polygon points="0,110 20,90 20,160 0,185" fill="#141414"/>
      <polygon points="0,230 20,210 20,266 0,266" fill="#141414"/>
    </svg>
  </section>

</body>
</html>
```